Design a modern, classy & professional business card for an online real estate agency, specializing in medium-luxury properties in Thailand and later in Singapore and UK.

Possible design ideas so far: (not essential)

- curved corner(s) to the card, white on front & turquoise on back or visa versa.

- front of card - clear and simple, company name in metallic grey/monochrome, logo graphic & company name on front in spot UV or embossed/debossed effect.

- back of card - large, close-cropped, 'ghost' patterns of the C-shaped curves of logo, or company name repeated on back of card in spot UV.

Target Market(s)

- young to middle-aged professionals mainly (but ideally should design should suit all)

- UK, US,EU,AUS & ASIAN mainly (but ideally should design should suit all countries)

Industry/Entity Type

Real Estate

Requirements
Must have
• THEME:
- Luxurious & Modern
- Clean & striking
- Unique & creative

INFO:
- Logo & company name on front
- Contact details on back:

Tobias Hennlund
Managing Director

www.velmontestates.asia
www.velmontestates.co.uk

Tel: 083-274-6159
email: tobias@velmontestates.asia

(contact details can be displayed in any order as suites design.)

Nice to have
• - curved corner(s) to the card, white on front & turquoise on back or visa versa.

Should not have
• - No generic images of properties, palm trees/coconut trees etc.

- No other other bold colors, except for main turquoise, grey, metallic white & black theme.

- No obvious business card templates

```html
<!DOCTYPE html>
<html lang="en">
<head>
<meta charset="utf-8">
<title>Velmont Estates – Business Card</title>
<link rel="stylesheet" href="https://fonts.googleapis.com/css2?family=Ubuntu:wght@400;500;700&display=swap">
<style>
  :root {
    --turquoise: #5fbfb8;
    --turquoise-light: #8ad6cf;
    --turquoise-dark: #3f9f99;
    --grey-metal: #8a8a8a;
    --grey-text: #4a4a4a;
    --ink: #2b2b2b;
    --paper: #ffffff;
    --ghost: #f1f2f2;
    --backdrop: #e7e9e9;
  }
  * { box-sizing: border-box; margin: 0; padding: 0; }
  html, body {
    width: 1200px; height: 913px; overflow: hidden;
    background: var(--backdrop);
    font-family: "Ubuntu", sans-serif;
  }
  .canvas {
    position: relative; width: 1200px; height: 913px;
  }
  .card {
    position: absolute; top: 306px;
    width: 520px; height: 300px;
    border-radius: 24px; overflow: hidden;
    box-shadow: 0 10px 28px rgba(0,0,0,.14);
  }

  /* Front */
  .card--front {
    left: 60px;
    background: linear-gradient(160deg, var(--turquoise-light) 0%, var(--turquoise) 55%, var(--turquoise-dark) 100%);
  }
  .brand {
    position: absolute; display: flex; align-items: center;
  }
  .card--front .brand { left: 70px; top: 112px; }
  .brand__mark { width: 76px; height: 76px; background: var(--paper); margin-right: 16px; }
  .brand__name {
    font-weight: 400; color: var(--grey-metal);
    font-size: 38px; letter-spacing: .5px; white-space: nowrap;
  }

  /* Back */
  .card--back { left: 620px; background: var(--paper); }
  .ghost-field {
    position: absolute; inset: 0;
    background: radial-gradient(ellipse at 45% 50%, var(--ghost) 0%, var(--paper) 80%);
  }
  .card--back .brand { left: 34px; top: 52px; }
  .card--back .brand__mark { width: 56px; height: 56px; background: var(--turquoise); margin-right: 12px; }
  .card--back .brand__name { font-size: 28px; }

  .person { position: absolute; left: 110px; top: 178px; text-align: right; }
  .person__name { color: var(--turquoise); font-weight: 700; font-size: 19px; }
  .person__title { color: var(--grey-text); font-size: 13px; margin-top: 4px; }

  .contacts {
    position: absolute; left: 300px; top: 104px;
    list-style: none; font-size: 11.5px; color: var(--ink);
  }
  .contacts li { display: flex; align-items: center; height: 22px; white-space: nowrap; }
  .contacts svg { width: 13px; height: 13px; margin-right: 8px; fill: var(--grey-text); flex: none; }
  .contacts .accent { color: var(--turquoise); }

  .band { position: absolute; left: 0; bottom: 0; width: 520px; height: 70px; }
</style>
</head>
<body>
<main class="canvas">

  <section class="card card--front" aria-label="Card front">
    <div class="brand">
      <span class="brand__mark"></span>
      <span class="brand__name">Velmont Estates</span>
    </div>
  </section>

  <section class="card card--back" aria-label="Card back">
    <div class="ghost-field" role="img" aria-label="Faint ghost pattern of interlocking curves"></div>

    <div class="brand">
      <span class="brand__mark"></span>
      <span class="brand__name">Velmont Estates</span>
    </div>

    <div class="person">
      <p class="person__name">Tobias Hennlund</p>
      <p class="person__title">Managing Director</p>
    </div>

    <ul class="contacts">
      <li>
        <svg viewBox="0 0 16 16"><path d="M3 2h3l1 4-2 1c1 2 2 3 4 4l1-2 4 1v3c0 1-1 1-2 1C7 14 2 9 2 4c0-1 0-2 1-2z"/></svg>
        083-274-6159
      </li>
      <li>
        <svg viewBox="0 0 16 16"><path d="M1 3h14v10H1z M1 3l7 6 7-6" stroke="#fff" stroke-width="1"/></svg>
        tobias@<span class="accent">velmontestates</span>.asia
      </li>
      <li>
        <svg viewBox="0 0 16 16"><circle cx="8" cy="8" r="7"/><path d="M1 8h14M8 1c-3 4-3 10 0 14M8 1c3 4 3 10 0 14" stroke="#fff" stroke-width="1" fill="none"/></svg>
        www.<span class="accent">velmontestates</span>.asia
      </li>
      <li>
        <svg viewBox="0 0 16 16"><circle cx="8" cy="8" r="7"/><path d="M1 8h14M8 1c-3 4-3 10 0 14M8 1c3 4 3 10 0 14" stroke="#fff" stroke-width="1" fill="none"/></svg>
        www.<span class="accent">velmontestates</span>.co.uk
      </li>
    </ul>

    <svg class="band" viewBox="0 0 520 70" preserveAspectRatio="none" aria-hidden="true">
      <polygon points="0,70 0,58 520,18 520,70" fill="var(--turquoise)"/>
      <polygon points="0,58 520,18 520,10 0,54" fill="var(--turquoise-light)"/>
    </svg>
  </section>

</main>
</body>
</html>
```